Venture Capital Investment Firm

We are looking to overhaul our existing website (substantially), with only using the same logos (which we can provide).
We are an investment firm that focuses on making loans to late stage technology companies. Our site should ultimately look like other venture capital firms, and look modern and fresh. We have an existing website www.norvellhub.com which this will be replacing, although we will be using a lot of the existing written content, and potentially the numbers of pages we will need, we are not wed to anything else. Please feel free to shoot any questions at any time and thank you in advance for your help!
Websites we like as examples:
https://www.tesmarkfund.com/
https://www.brindlewoodpartners.com/
Target Market(s)
Potential investors who will invest in our firm, as well as potentially companies that are looking to borrow money from us.
Coding
Coded - Design and coding required
Number of Pages Required
5+ page
Colors
Designer to choose colors to be used in the design.
Look and feel

```html
<!DOCTYPE html>
<html lang="en">
<head>
<meta charset="utf-8">
<title>Norvell Capital — Investment Partners</title>
<link rel="stylesheet" href="https://fonts.googleapis.com/css2?family=Cinzel:wght@400;600;700&family=Roboto:wght@400;500&family=Tinos&display=swap">
<style>
:root{
  --navy:#070637;
  --navy-soft:#12114a;
  --dark:#1c1c22;
  --white:#ffffff;
  --text:#555560;
  --muted:#6f6f78;
  --accent:#f08a24;
  --sky:#2aa3dc;
  --line:#d9d9de;
}
*{margin:0;padding:0;box-sizing:border-box}
html,body{width:1200px;height:4651px;overflow:hidden}
body{position:relative;background:var(--white);font-family:'Roboto',sans-serif;color:var(--text)}
.abs{position:absolute}
.btn{position:absolute;display:flex;align-items:center;justify-content:center;font-family:'Cinzel',serif;font-weight:700;color:var(--white);background:var(--navy);border-radius:4px;white-space:nowrap}

/* Hero */
.hero-bg{position:absolute;left:0;top:0}
.brand{position:absolute;left:90px;top:28px;display:flex;align-items:center;gap:10px;color:var(--white);font-family:'Cinzel',serif;font-size:19px;font-weight:600;white-space:nowrap}
.brand .dot{width:32px;height:32px;border-radius:50%;border:3px solid var(--white)}
.nav{position:absolute;left:381px;top:38px;display:flex;font-family:'Cinzel',serif;font-size:17px;color:var(--white);white-space:nowrap}
.nav span{margin-right:33px}
.nav .active{color:var(--accent)}
.hero-title{position:absolute;left:90px;top:188px;font-family:'Cinzel',serif;font-size:56px;font-weight:600;color:var(--white);letter-spacing:1px;white-space:nowrap}
.hero-text{position:absolute;left:90px;top:274px;width:400px;font-size:15px;line-height:28px;color:var(--white)}
.hero-btn{position:absolute;left:90px;top:382px;width:235px;height:62px;border:2px solid var(--white);border-radius:6px;display:flex;align-items:center;justify-content:center;font-family:'Cinzel',serif;font-weight:700;font-size:22px;color:var(--white)}
.hero-arrow{position:absolute;top:494px;width:58px;height:58px;border:2px solid var(--white);border-radius:50%}
.hero-photo{position:absolute;left:608px;top:130px;width:498px;height:498px;border-radius:50%;background:radial-gradient(circle at 40% 40%,#b9a58e,#5c5046 55%,#2b2a2e)}

/* About */
.about-frame{position:absolute;left:90px;top:852px;width:383px;height:361px;border:14px solid var(--navy);border-right:none;border-top:none}
.about-frame::before{content:"";position:absolute;left:-14px;top:0;width:60px;height:14px;background:var(--navy)}
.about-frame::after{content:"";position:absolute;right:0;bottom:-14px;width:14px;height:40px;background:var(--navy)}
.about-photo{position:absolute;left:150px;top:816px;width:382px;height:361px;background:linear-gradient(135deg,#d9c2a3,#9b8a78 55%,#3e4352)}
.h-section{font-family:'Cinzel',serif;color:var(--navy);font-weight:600}
.about-title{position:absolute;left:569px;top:806px;font-size:44px}
.about-text{position:absolute;left:569px;top:882px;width:540px;font-size:14.5px;line-height:32.5px;color:var(--muted);text-align:justify}

/* Strategy */
.strategy{position:absolute;left:0;top:1321px;width:1200px;height:688px;background:linear-gradient(180deg,#26262c,#18181d)}
.strategy-title{position:absolute;left:0;width:1200px;top:1370px;text-align:center;font-size:42px;color:var(--white)}
.strategy-sub{position:absolute;left:150px;width:900px;top:1434px;text-align:center;font-size:19px;line-height:36px;color:var(--white)}
.card{position:absolute;top:1552px;width:278px;height:365px;background:var(--white);border-radius:4px}
.card-icon{position:absolute;left:114px;top:-24px;width:50px;height:50px;border-radius:50%;background:var(--navy);border:2px solid var(--white)}
.card-title{position:absolute;left:0;width:100%;top:56px;text-align:center;font-family:'Cinzel',serif;font-size:23px;line-height:30px;color:var(--navy)}
.card-rule{position:absolute;left:70px;width:138px;top:136px;height:1px;background:var(--navy)}
.card-text{position:absolute;left:14px;width:250px;top:155px;text-align:center;font-size:12.5px;line-height:27.5px;color:var(--muted)}
.card-btn{left:78px;width:123px;height:34px;top:342px;font-size:14px}

/* Team */
.team-title{position:absolute;left:0;width:1200px;top:2106px;text-align:center;font-size:42px}
.member{position:absolute;top:2226px;width:296px;text-align:center}
.member .photo{width:296px;height:296px;border-radius:50%;background:radial-gradient(circle at 50% 38%,#8a8a8a,#3a3a3a 55%,#111)}
.member .photo.hover{background:radial-gradient(circle at 50% 38%,#3b3a6a,#14134a 60%,#070637)}
.member .name{margin-top:20px;font-family:'Cinzel',serif;font-size:23px;color:var(--navy)}
.member .role{margin-top:2px;font-size:13.5px;font-weight:500;color:var(--navy)}

/* Newsletter */
.newsletter{position:absolute;left:0;top:2693px;width:1200px;height:273px;background:var(--navy)}
.nl-title{position:absolute;left:0;width:1200px;top:2730px;text-align:center;font-size:42px;color:var(--white)}
.nl-text{position:absolute;left:0;width:1200px;top:2794px;text-align:center;font-size:21px;color:var(--white)}
.nl-form{position:absolute;left:301px;top:2850px;width:597px;height:65px;background:var(--white);border-radius:6px}
.nl-form .ph{position:absolute;left:14px;top:22px;font-size:16px;color:#666}
.nl-form .btn{left:413px;top:4px;width:180px;height:57px;font-size:22px}

/* News */
.news-title{position:absolute;left:0;width:1200px;top:3060px;text-align:center;font-size:46px}
.news-card{position:absolute;top:3179px;width:326px;height:509px;background:var(--white);box-shadow:0 2px 8px rgba(0,0,0,.12)}
.news-card .img{height:202px}
.news-card .badge{position:absolute;right:22px;top:172px;width:58px;height:58px;border-radius:50%;background:var(--sky);color:var(--white);font-size:12.5px;line-height:15px;display:flex;flex-direction:column;align-items:center;justify-content:center;text-align:center}
.news-card h3{position:absolute;left:7px;right:7px;top:236px;font-family:'Cinzel',serif;font-weight:400;font-size:19px;line-height:28px;color:var(--navy);letter-spacing:.5px}
.news-card p{position:absolute;left:7px;right:7px;top:328px;font-size:13px;line-height:27px;color:var(--muted);text-align:justify}
.news-card .meta{position:absolute;left:10px;right:10px;top:457px;display:flex;justify-content:space-between;font-family:'Tinos',serif;font-size:17px;color:#222}
.meta span{display:flex;align-items:center;gap:8px}
.dots{position:absolute;left:570px;top:3719px;display:flex;gap:7px}
.dots i{width:12px;height:12px;border-radius:50%;background:#111}
.dots i.off{background:var(--white);border:2px solid #111}

/* Contact */
.contact-title{position:absolute;left:112px;top:3904px;font-size:44px;line-height:55px}
.contact-rule{position:absolute;left:116px;top:4023px;width:2px;height:110px;background:var(--navy)}
.contact-info{position:absolute;left:146px;top:4036px;font-size:16px;line-height:27px;color:#333;border-collapse:collapse}
.contact-info td{vertical-align:top;padding-right:10px}
.contact-btn{left:116px;top:4170px;width:188px;height:55px;font-size:18px}
.map{position:absolute;left:542px;top:3841px;width:658px;height:460px;background:linear-gradient(135deg,#ecebe6,#e2e6ea 60%,#eae4d2)}

/* Footer */
.footer{position:absolute;left:0;top:4301px;width:1200px;height:350px;background:var(--navy);color:var(--white)}
.f-brand{position:absolute;left:90px;top:4382px;display:flex;align-items:center;gap:12px;font-family:'Cinzel',serif;font-size:27px;font-weight:600;color:var(--white);white-space:nowrap}
.f-brand .dot{width:42px;height:42px;border-radius:50%;border:3px solid var(--white)}
.f-text{position:absolute;left:90px;top:4462px;width:330px;font-size:12px;line-height:20px;color:var(--white)}
.f-col{position:absolute;top:4380px;color:var(--white)}
.f-col h4{font-family:'Cinzel',serif;font-weight:400;font-size:24px;margin-bottom:14px;white-space:nowrap}
.f-col li{list-style:none;font-size:13.5px;line-height:27px}
.copy{position:absolute;left:0;width:1200px;top:4610px;text-align:center;font-size:15px;color:var(--white)}
</style>
</head>
<body>

<!-- Hero -->
<svg class="hero-bg" width="1200" height="710" viewBox="0 0 1200 710" aria-hidden="true">
  <path d="M0 0 H1101 C1000 260 780 640 0 706 Z" fill="#070637"/>
</svg>
<div class="brand"><span class="dot"></span>Norvell Capital</div>
<nav class="nav"><span class="active">Home</span><span>Strategy</span><span>About Us</span><span>Team</span><span>News</span><span>Contact</span><span>Investors</span></nav>
<h1 class="hero-title">Norvell Capital</h1>
<p class="hero-text">Our team was also early to recognize the potential of “non-core” assets beyond drug royalties, acquiring over $300M of branded generics offering predictable cash</p>
<div class="hero-btn">Get A Started</div>
<svg class="hero-arrow" style="left:90px" viewBox="0 0 58 58" aria-label="Previous"><path d="M38 29H20M26 23l-6 6 6 6" stroke="#fff" stroke-width="3" fill="none"/></svg>
<svg class="hero-arrow" style="left:174px" viewBox="0 0 58 58" aria-label="Next"><path d="M20 29h18M32 23l6 6-6 6" stroke="#fff" stroke-width="3" fill="none"/></svg>
<div class="hero-photo" role="img" aria-label="Photo of colleagues reviewing financial charts at a desk"></div>

<!-- About -->
<div class="about-frame"></div>
<div class="about-photo" role="img" aria-label="Photo of two business partners reviewing documents"></div>
<h2 class="h-section about-title">About Us</h2>
<p class="about-text">Norvell Capital is a private investment firm unique in its dual focus on life science and technology credit opportunities. Our ambidextrous approach to investing reflects a broad recognition and appreciation for the critical role intellectual property plays in the successful commercialization of products. We apply our extensive industry expertise to assess the revenue visibility created by these assets and offer a range of creative financing solutions.A pioneer in providing life science structured credit beginning in 2004, the Norvell Capital team.</p>
<div class="btn" style="left:569px;top:1146px;width:178px;height:54px;font-size:18px">Read More</div>

<!-- Strategy -->
<section class="strategy" role="img" aria-label="Dark background photo of a city skyline"></section>
<h2 class="h-section strategy-title">Strategy</h2>
<p class="strategy-sub">We seek to fill a void in the capital markets where too often complexity and perceived risk penalize innovative companies with proven products.</p>

<div class="card" style="left:135px">
  <svg class="card-icon" viewBox="0 0 50 50" aria-hidden="true"><rect x="16" y="16" width="18" height="18" rx="2" stroke="#fff" stroke-width="2" fill="none"/><path d="M20 22h10M20 27h10" stroke="#fff" stroke-width="2"/></svg>
  <div class="card-title">Structured<br>Credit</div>
  <div class="card-rule"></div>
  <p class="card-text">We offer revenue-generating companies in the life science and technology industries be spoke loans which offer multiple benefits Our financings are designed to allow our transaction partners to realize the value of businesses</p>
  <div class="btn card-btn">Read More</div>
</div>
<div class="card" style="left:471px">
  <svg class="card-icon" viewBox="0 0 50 50" aria-hidden="true"><path d="M19 14v22M19 15l13 8-13 8" stroke="#fff" stroke-width="2" fill="none"/></svg>
  <div class="card-title">Milestones &amp;<br>Royalties</div>
  <div class="card-rule"></div>
  <p class="card-text">We offer owners of milestones &amp; royalty rights the ability to monetize or securitize future cash flows ranging from $10-250M.Norvell Capital has the ability to structure its transactions in a variety of ways depending on the specific attributes</p>
  <div class="btn card-btn">Read More</div>
</div>
<div class="card" style="left:805px">
  <svg class="card-icon" viewBox="0 0 50 50" aria-hidden="true"><circle cx="25" cy="25" r="6" fill="#fff"/><circle cx="25" cy="25" r="12" stroke="#fff" stroke-width="2" stroke-dasharray="4 3" fill="none"/></svg>
  <div class="card-title">Legacy<br>Assets</div>
  <div class="card-rule"></div>
  <p class="card-text">We offer companies with mature, “non-core” assets upfront capital in exchange for products that are no longer strategic to their businesses. The partners of Norvell Capital have successfully acquired over $300M of these “legacy</p>
  <div class="btn card-btn">Read More</div>
</div>

<!-- Team -->
<h2 class="h-section team-title">Team</h2>
<div class="member" style="left:92px"><div class="photo" role="img" aria-label="Portrait of Daniel Marsh"></div><div class="name">Daniel Marsh</div><div class="role">MANAGING PARTNER</div></div>
<div class="member" style="left:453px">
  <div class="photo hover" role="img" aria-label="Portrait of Samir Okafor"></div>
  <svg class="abs" style="left:103px;top:134px" width="90" height="34" viewBox="0 0 90 34" aria-hidden="true">
    <rect x="2" y="5" width="32" height="24" rx="3" stroke="#fff" stroke-width="2.5" fill="none"/><path d="M3 7l15 12 15-12" stroke="#fff" stroke-width="2.5" fill="none"/>
    <rect x="58" y="2" width="30" height="30" rx="5" stroke="#fff" stroke-width="2.5" fill="none"/>
  </svg>
  <div class="name">Samir Okafor</div><div class="role">MANAGING PARTNER</div>
</div>
<div class="member" style="left:814px"><div class="photo" role="img" aria-label="Portrait of Henry Cole"></div><div class="name">Henry Cole</div><div class="role">PARTNER</div></div>

<!-- Newsletter -->
<section class="newsletter"></section>
<h2 class="h-section nl-title" style="color:#fff">Join Our Newsletter</h2>
<p class="nl-text">We are an investment firm that focuses on making loans to late stage technology companies.</p>
<div class="nl-form"><span class="ph">Enter Your Email</span><div class="btn">Subscribe</div></div>

<!-- News -->
<h2 class="h-section news-title">Recent News</h2>
<article class="news-card" style="left:88px">
  <div class="img" role="img" aria-label="Photo of a laptop and printed charts on a desk" style="background:linear-gradient(135deg,#e6e8ec,#a9b3c0)"></div>
  <div class="badge">April<br>2018</div>
  <h3>Norvell Capital completes structured debt investment in Lumenpath</h3>
  <p>Norvell Capital Partners (“Norvell Capital”) announced today that it has completed a structured debt investment in Lumenpath, Inc. (“Lumenpath”), the leader in employee.</p>
  <div class="meta"><span>&#9679; Lorem ipsum</span><span>&#9632; 04 Comments</span></div>
</article>
<article class="news-card" style="left:435px">
  <div class="img" role="img" aria-label="Photo of a hand writing over printed financial charts" style="background:linear-gradient(135deg,#dfe1e6,#8f96a3)"></div>
  <div class="badge">Oct.<br>2016</div>
  <h3>Norvell Capital completes $22,000,000 structured debt investment in Surveyline</h3>
  <p>Norvell Capital Partners (“Norvell Capital”) announced today that it has completed a $22,000,000 structured debt investment in Surveyline AS (“Surveyline”).</p>
  <div class="meta"><span>&#9679; Lorem ipsum</span><span>&#9632; 04 Comments</span></div>
</article>
<article class="news-card" style="left:780px">
  <div class="img" role="img" aria-label="Photo of coin stacks with small plants growing" style="background:linear-gradient(135deg,#c9c27a,#6b6a2e 60%,#3b3a22)"></div>
  <div class="badge">July<br>2015</div>
  <h3>Norvell Capital closes inaugural $100,000,000 investment vehicle</h3>
  <p>Norvell Capital Partners, LLC (“Norvell Capital” or “NorvCap”), an investment firm focused on structured investment opportunities in the life sciences and technology sectors.</p>
  <div class="meta"><span>&#9679; Lorem ipsum</span><span>&#9632; 04 Comments</span></div>
</article>
<div class="dots"><i></i><i class="off"></i><i></i></div>

<!-- Contact -->
<h2 class="h-section contact-title">Get In Touch<br>With Us</h2>
<div class="contact-rule"></div>
<table class="contact-info">
  <tr><td>Address:</td><td>420 Harbor Lane #210<br>Fairview, CA 94000</td></tr>
  <tr><td>Phone:</td><td>555 010 2040</td></tr>
  <tr><td>Email:</td><td>hello@norvellhub.com</td></tr>
</table>
<div class="btn contact-btn">Send Message</div>
<div class="map" role="img" aria-label="Street map showing the office location"></div>

<!-- Footer -->
<footer class="footer"></footer>
<div class="f-brand"><span class="dot"></span>Norvell Capital</div>
<p class="f-text">Our team was also early to recognize the potential of “non-core” assets beyond drug royalties, acquiring over $300M of branded generics</p>
<div class="f-col" style="left:498px"><h4>Quicks Links</h4><ul><li>Home</li><li>Strategy</li><li>About Us</li><li>Team</li><li>News</li><li>Contact</li></ul></div>
<div class="f-col" style="left:722px"><h4>About Us</h4><ul><li>About Us</li><li>Blog</li><li>Contact Us</li><li>Meet our Team</li></ul></div>
<div class="f-col" style="left:911px"><h4>Other Links</h4><ul><li>General Inquiries</li><li>Media Inquiries</li><li>Transaction Opportunities</li><li>Media Inquiries</li></ul></div>
<p class="copy">© 2019 Norvell Capital Partners Llc. &nbsp;All Rights Reserved | Legal Disclaimer</p>

</body>
</html>
```